Aunt Wilma's Ember-Kissed Husk Shack Concession Trailer Logo Wraps

Looking to put my design concept into a final production-ready format for vinyl-based logo "wrap" on the exterior of a 7x12 black concession trailer selling farm-fresh corn on the cob slathered in flavor flamboyance, corn in a cup, corn over crushed snacks (Crunvels, Zaplins, Puffnars, etc.) served in the bags, fire-roasted street corn (Mexican elotes), corn grits, corn chowder, cornbread, corndogs. I have my fonts and colors and a flame graphic I've roughly edited/reworked attempting to make it work and need a design pro to bring it all together for me. The approximate size of the graphics on the four sides of the trailer will be: the serving window when closed (48"L x 24"H); front (48"x48"); full right side (11'x5'); door (6'x2') and possibly the left side next to door (3'x5'). Pictures uploaded.
Target Market(s)
Food truck festivals, private catering gigs, fairs, farm markets, concerts, etc.
Font styles to use
Other font styles liked:
- flame fetish, Algerian
Requirements
Must have
- My color scheme as depicted in uploaded files, flame fetish font uploaded (will consider similar fonts), flame/fire artwork, bright bold colors that pop against a black background
Nice to have
- straight line of flames on each side of the "fire-roasted" text, flowing from the first and last letter

```html
<!DOCTYPE html>
<html lang="en">
<head>
<meta charset="utf-8">
<title>Aunt Wilma's Ember-Kissed Husk Shack</title>
<link rel="stylesheet" href="https://fonts.googleapis.com/css2?family=Playball&family=Kaushan+Script&family=Rye&display=swap">
<style>
  :root {
    --frame-orange: #f7820f;
    --panel-black: #000000;
    --band-black: #070707;
    --title-blue: #4f9ff2;
    --glow-orange: #ff8a1c;
    --corn-yellow: #f5e614;
    --flame-red: #c8260a;
    --flame-orange: #f47a12;
    --flame-gold: #ffc52a;
  }
  html, body {
    margin: 0;
    padding: 0;
    width: 1200px;
    height: 600px;
    overflow: hidden;
    background: var(--frame-orange);
  }
  .sign {
    position: relative;
    width: 1200px;
    height: 600px;
    background: var(--frame-orange);
  }
  .sign-panel {
    position: absolute;
    left: 25px;
    top: 25px;
    width: 1150px;
    height: 550px;
    background: var(--panel-black);
    overflow: hidden;
  }
  .flame-band {
    position: absolute;
    left: 0;
    top: 115px;
    width: 1150px;
    height: 231px;
    background:
      radial-gradient(ellipse 220px 210px at 60px 231px, var(--flame-gold) 0%, var(--flame-orange) 40%, rgba(200,38,10,0.6) 65%, rgba(0,0,0,0) 100%),
      radial-gradient(ellipse 240px 220px at 1090px 231px, var(--flame-gold) 0%, var(--flame-orange) 40%, rgba(200,38,10,0.6) 65%, rgba(0,0,0,0) 100%),
      linear-gradient(to bottom, rgba(0,0,0,0) 35%, rgba(200,38,10,0.55) 70%, var(--flame-orange) 92%, var(--flame-gold) 100%);
  }
  .lower-band {
    position: absolute;
    left: 0;
    top: 321px;
    width: 1150px;
    height: 229px;
    background: var(--band-black);
  }
  .owner-name {
    position: absolute;
    left: 0;
    top: 18px;
    width: 1150px;
    margin: 0;
    text-align: center;
    font-family: "Playball", cursive;
    font-weight: 400;
    font-size: 160px;
    line-height: 1;
    color: var(--title-blue);
  }
  .roast-style {
    position: absolute;
    left: 0;
    top: 208px;
    width: 1150px;
    margin: 0;
    text-align: center;
    font-family: "Kaushan Script", cursive;
    font-size: 108px;
    line-height: 1;
    color: #0a0a0a;
    text-shadow:
      0 0 4px var(--glow-orange),
      0 0 8px var(--glow-orange),
      0 0 14px var(--glow-orange);
  }
  .business-type {
    position: absolute;
    left: 0;
    top: 345px;
    width: 1150px;
    margin: 0;
    text-align: center;
    font-family: "Rye", serif;
    font-weight: 400;
    font-size: 104px;
    line-height: 1;
    letter-spacing: 6px;
    color: var(--corn-yellow);
    text-shadow: 4px 5px 0 var(--band-black), 6px 7px 0 var(--corn-yellow);
  }
  .tagline {
    position: absolute;
    left: 0;
    top: 476px;
    width: 1150px;
    margin: 0;
    text-align: center;
    font-family: "Kaushan Script", cursive;
    font-size: 36px;
    line-height: 1;
    color: var(--corn-yellow);
  }
</style>
</head>
<body>
  <div class="sign">
    <div class="sign-panel">
      <div class="flame-band" role="img" aria-label="Row of roaring flames with glowing embers along the sides"></div>
      <div class="lower-band"></div>
      <h1 class="owner-name">Aunt Wilma's</h1>
      <p class="roast-style">ember-kissed</p>
      <p class="business-type">HUSK SHACK</p>
      <p class="tagline">Sweet kernels charred golden and piled high with zest</p>
    </div>
  </div>
</body>
</html>
```